Business Card Design for Occupational Medicine Start Up Company

We need to design a professional business card. We are a healthcare company providing occupational medicine services to blue collar industries. We are professional, efficient and high quality service providers.

Target Market(s)

Blue Collar Industry: Shipbuilding, Ports, Trucking Companies; The Executives and Safety Officers for these companies

Industry/Entity Type

Healthcare

Contact Information for Business Card

Logo, Name, Title, Email, Phone

Other font styles liked:
• Please match our Brand Guide

Requirements
Must have
• Our Company Colors and Logo

```html
<!DOCTYPE html>
<html lang="en">
<head>
<meta charset="utf-8">
<title>Shiftwell Clinics – Business Card</title>
<link rel="stylesheet" href="https://fonts.googleapis.com/css2?family=Montserrat:wght@700&family=Open+Sans:wght@400;600&display=swap">
<style>
  :root {
    --backdrop: #1c1c1e;
    --navy: #1a2a8c;
    --navy-deep: #14206e;
    --royal: #1f2f9a;
    --gold: #f3b23b;
    --sky: #3fa7e0;
    --ink: #2b2b2b;
    --paper: #ffffff;
    --faint: #e4e9f4;
  }
  * { margin: 0; padding: 0; box-sizing: border-box; }
  html, body {
    width: 1200px; height: 900px; overflow: hidden;
    background: var(--backdrop);
  }
  .stage { position: relative; width: 1200px; height: 900px; }

  .card {
    position: absolute;
    width: 620px; height: 354px;
    overflow: hidden;
    box-shadow: 0 18px 40px rgba(0,0,0,0.55);
  }

  /* Front */
  .card--front {
    left: 170px; top: 80px;
    background: linear-gradient(135deg, var(--royal), var(--navy-deep));
    display: flex; align-items: center; justify-content: center;
  }
  .brand {
    display: flex; align-items: center; gap: 14px;
    font-family: 'Montserrat', sans-serif; font-weight: 700;
  }
  .brand__mark { border-radius: 50%; flex: none; }
  .brand__name { line-height: 1.05; letter-spacing: 0.04em; }
  .brand__name span { display: block; }
  .card--front .brand { color: var(--paper); }
  .card--front .brand__mark { width: 46px; height: 46px; background: var(--gold); }
  .card--front .brand__name { font-size: 34px; }
  .card--front .brand__name span + span { font-size: 16px; letter-spacing: 0.42em; text-align: center; }

  /* Back */
  .card--back {
    left: 410px; top: 476px;
    background: var(--paper);
  }
  .card--back .brand { position: absolute; left: 40px; top: 30px; color: var(--navy); }
  .card--back .brand__mark { width: 38px; height: 38px; background: var(--gold); }
  .card--back .brand__name { font-size: 22px; }
  .card--back .brand__name span + span { font-size: 10px; letter-spacing: 0.42em; text-align: center; }

  .backdrop-name {
    position: absolute; right: 30px; top: 110px;
    font-family: 'Montserrat', sans-serif; font-weight: 700;
    font-size: 30px; letter-spacing: 0.04em;
    color: var(--faint);
  }

  .holder { position: absolute; left: 44px; top: 150px; }
  .holder__name {
    font-family: 'Montserrat', sans-serif; font-weight: 700;
    font-size: 26px; color: var(--navy);
  }
  .holder__title {
    font-family: 'Open Sans', sans-serif; font-size: 12px; color: var(--ink);
    margin-top: 2px;
  }

  .contacts {
    position: absolute; left: 46px; top: 220px;
    list-style: none;
    font-family: 'Open Sans', sans-serif; font-size: 14px; color: var(--ink);
  }
  .contacts li { display: flex; align-items: center; gap: 14px; height: 24px; }
  .contacts svg { width: 14px; height: 14px; fill: var(--navy); }

  .footer-band {
    position: absolute; left: 0; right: 0; bottom: 0; height: 62px;
    background: linear-gradient(180deg, var(--gold) 0%, var(--navy) 50%, var(--sky) 100%);
  }
</style>
</head>
<body>
<main class="stage">

  <section class="card card--front" aria-label="Card front">
    <div class="brand">
      <span class="brand__mark"></span>
      <p class="brand__name"><span>SHIFTWELL</span><span>CLINICS</span></p>
    </div>
  </section>

  <section class="card card--back" aria-label="Card back">
    <p class="backdrop-name" aria-hidden="true">SHIFTWELL</p>

    <div class="brand">
      <span class="brand__mark"></span>
      <p class="brand__name"><span>SHIFTWELL</span><span>CLINICS</span></p>
    </div>

    <div class="holder">
      <h1 class="holder__name">Marisol</h1>
      <p class="holder__title">Manager</p>
    </div>

    <ul class="contacts">
      <li>
        <svg viewBox="0 0 24 24" aria-hidden="true"><path d="M6.6 10.8a15.1 15.1 0 0 0 6.6 6.6l2.2-2.2a1 1 0 0 1 1-.25 11.4 11.4 0 0 0 3.6.57 1 1 0 0 1 1 1V20a1 1 0 0 1-1 1A17 17 0 0 1 3 4a1 1 0 0 1 1-1h3.5a1 1 0 0 1 1 1c0 1.25.2 2.45.57 3.57a1 1 0 0 1-.25 1z"/></svg>
        555 210 4837
      </li>
      <li>
        <svg viewBox="0 0 24 24" aria-hidden="true"><path d="M2 5h20v14H2z M3.5 6.5 12 13l8.5-6.5" stroke="#fff" stroke-width="1.6"/></svg>
        hello@shiftwellcare.com
      </li>
    </ul>

    <div class="footer-band" role="img" aria-label="Decorative swoosh stripes in gold, navy and sky blue along the bottom edge"></div>
  </section>

</main>
</body>
</html>
```